Business Card Design - Photographer

I am a landscape photographer and I require a business card design. 

I require two designs:
1)  a double sided business card
 and
b)  a single sided business card 

The single sided design can either be the same as the double sided (with just one side having all the information)....or it can be an entire new design. Its up to you.

My corporate colours are (CMYK):

Blue   69, 32, 0, 0
Grey  72,  64,  47,  31
Green  32,  2,  91,  0
Yellow   0, 19, 92, 0
Orange  0, 39, 75, 0

Colour space in final file should be in CMYK.

The details that need to be included on the card:

- Use the provided Logo
- Name: Wiktor Baranowski
- Email:   sales@vistalumeworks.com.au
- Website:    vistalumeworks.com.au
- Twitter:    twitter.com/vistalumeworks
- Facebook:   facebook.com/vistalumeworks
- Mobile  0417 539 662

Please use the attached template to design the logo to the specified size, including the marked bleed lines. I have also attached my logo in PNG (transparent background) and ai format for you to use.

The final file should be:
- Photoshop version with layers so I can edit the name/text etc. All non vector files should be high resolution at 1039 x 697 pixels at 300 dpi.

I also require a file as:
- Vector based PDF

Anyway questions please contact me.

Thank you

Industry/Entity Type

Landscape

Logo styles of interest
Pictorial/Combination Logo
Abstract Logo
Wordmark Logo
Lettermark Logo
Requirements
Must have
• The details that need to be included on the card:

- Use the provided Logo
- Name: Wiktor Baranowski
- Email: sales@vistalumeworks.com.au
- Website: vistalumeworks.com.au
- Twitter: twitter.com/vistalumeworks
- Facebook: facebook.com/vistalumeworks
- Mobile 0417 539 662

```html
<!DOCTYPE html>
<html lang="en">
<head>
<meta charset="utf-8">
<title>Wiktor Baranowski – Business Card</title>
<link rel="stylesheet" href="https://fonts.googleapis.com/css2?family=Cinzel:wght@400;600;700&display=swap">
<style>
  :root {
    --backdrop: #838488;
    --card: #ffffff;
    --slate: #3c4052;
    --lime: #b8d23c;
    --sky: #3d95d3;
    --shadow: rgba(0, 0, 0, 0.35);
  }
  * { margin: 0; padding: 0; box-sizing: border-box; }
  html, body {
    width: 976px; height: 1200px; overflow: hidden;
    background: var(--backdrop);
    font-family: "Cinzel", "Times New Roman", serif;
  }
  .stage { position: relative; width: 976px; height: 1200px; }
  .card {
    position: absolute; background: var(--card);
    border-radius: 28px; overflow: hidden;
    box-shadow: 3px 5px 8px var(--shadow);
  }
  .card--front { left: 105px; top: 88px; width: 817px; height: 465px; }
  .card--back  { left: 102px; top: 642px; width: 817px; height: 466px; }

  .swoosh { position: absolute; inset: 0; width: 100%; height: 100%; }

  .brand-mark { position: absolute; border-radius: 50%; background: var(--slate); }
  .card--front .brand-mark { left: 163px; top: 45px; width: 165px; height: 165px; }

  .brand-lockup {
    position: absolute; left: 22px; top: 226px; width: 445px;
    text-align: center; color: var(--slate);
  }
  .person-name {
    font-size: 37px; font-weight: 400; line-height: 48px; white-space: nowrap;
  }
  .brand-rule { height: 2px; background: var(--slate); margin-top: 4px; }
  .tagline {
    margin-top: 11px; font-size: 15px; font-weight: 700;
    letter-spacing: 3px; line-height: 18px; white-space: nowrap;
  }

  .web { position: absolute; white-space: nowrap; font-weight: 400; }
  .web .big { font-size: 1.35em; font-weight: 600; }
  .card--front .web { right: 30px; top: 410px; font-size: 17px; color: #fff; }

  .card--back .brand-mark { left: 348px; top: 58px; width: 120px; height: 120px; }

  .contact-list {
    position: absolute; left: 0; top: 224px; width: 100%;
    list-style: none; text-align: center; color: var(--slate);
    font-size: 17px; letter-spacing: 0.5px;
  }
  .contact-list li {
    height: 36px; display: flex; align-items: center; justify-content: center; gap: 10px;
  }
  .contact-icon { width: 16px; height: 16px; flex: none; }
  .card--back .web {
    left: 0; width: 100%; text-align: center; top: 400px;
    font-size: 17px; color: var(--lime);
  }
</style>
</head>
<body>
<main class="stage">

  <section class="card card--front" aria-label="Card front">
    <svg class="swoosh" viewBox="0 0 817 465" preserveAspectRatio="none" aria-hidden="true">
      <path d="M0,390 C240,425 560,395 817,232 L817,465 L0,465 Z" fill="var(--lime)"/>
      <path d="M0,385 C250,418 560,370 817,165 L817,215 C560,385 260,425 0,389 Z" fill="var(--slate)"/>
    </svg>
    <div class="brand-mark" aria-hidden="true"></div>
    <div class="brand-lockup">
      <div class="person-name">WIKTOR BARANOWSKI</div>
      <div class="brand-rule"></div>
      <div class="tagline">FINE ART PHOTOGRAPHY</div>
    </div>
    <div class="web">www.<span class="big">VISTALUMEWORKS</span>.com.au</div>
  </section>

  <section class="card card--back" aria-label="Card back">
    <div class="brand-mark" aria-hidden="true"></div>
    <ul class="contact-list">
      <li>
        <svg class="contact-icon" viewBox="0 0 16 16" aria-hidden="true">
          <rect x="1" y="4" width="14" height="10" fill="none" stroke="var(--sky)" stroke-width="1.4"/>
          <path d="M1,4 L8,10 L15,4" fill="none" stroke="var(--sky)" stroke-width="1.4"/>
        </svg>
        <span>sales@vistalumeworks.com.au</span>
      </li>
      <li>
        <svg class="contact-icon" viewBox="0 0 16 16" aria-hidden="true"><rect x="1" y="1" width="14" height="14" rx="2" fill="#7fc3e8"/></svg>
        <span>twitter.com/vistalumeworks</span>
      </li>
      <li>
        <svg class="contact-icon" viewBox="0 0 16 16" aria-hidden="true"><rect x="1" y="1" width="14" height="14" rx="2" fill="#3b5a98"/></svg>
        <span>facebook.com/vistalumeworks</span>
      </li>
      <li>
        <svg class="contact-icon" viewBox="0 0 16 16" aria-hidden="true">
          <rect x="3.5" y="1" width="9" height="14" rx="1.5" fill="var(--sky)"/>
          <rect x="5" y="3" width="6" height="4" fill="#fff"/>
          <rect x="5" y="9" width="6" height="4" fill="#cfe6f6"/>
        </svg>
        <span>0417 539 662</span>
      </li>
    </ul>
    <div class="web">www.<span class="big">VISTALUMEWORKS</span>.com.au</div>
  </section>

</main>
</body>
</html>
```